Birchline Septic Solutions

Would like to see some single sided ones but would also like to see some double sided with one sided only being the logo. Owners name is Colin Vandro. Phone number is 555-214-0387
Services are pumping, inspections, installs, and repairs

Contact Information for Business Card

555-241-0387 Colin Vandro Maple Hollow, OH

```html
<!DOCTYPE html>
<html lang="en">
<head>
<meta charset="utf-8">
<title>Birchline Septic Solutions — Business Card</title>
<link rel="stylesheet" href="https://fonts.googleapis.com/css2?family=Montserrat:wght@400;500;700;800&display=swap">
<style>
  :root {
    --backdrop: #4a4a49;
    --card: #161616;
    --teal: #2bbdb6;
    --white: #ffffff;
    --soft-white: #e9e9e9;
  }
  * { margin: 0; padding: 0; box-sizing: border-box; }
  html, body {
    width: 1200px; height: 801px; overflow: hidden;
    background: var(--backdrop);
    font-family: "Montserrat", Arial, sans-serif;
  }
  .sheet {
    width: 1200px; height: 801px;
    display: flex; align-items: center; justify-content: center; gap: 48px;
  }
  .card {
    width: 540px; height: 309px;
    background: var(--card);
    border-radius: 18px;
    border: 2px solid var(--teal);
    position: relative;
    overflow: hidden;
  }
  /* Contact side */
  .card--contact { display: flex; }
  .contact__brand {
    width: 54%;
    display: flex; align-items: center; justify-content: center;
    padding-left: 22px;
  }
  .contact__divider {
    width: 1.5px; background: var(--teal);
    margin: 70px 0;
  }
  .contact__details {
    flex: 1;
    padding: 60px 0 0 24px;
    color: var(--soft-white);
  }
  .brand-name {
    display: flex; align-items: center; gap: 10px;
    color: var(--white);
    font-weight: 800;
    text-transform: uppercase;
    line-height: 1.05;
    letter-spacing: 0.04em;
  }
  .brand-name__mark {
    flex: none; border-radius: 50%; background: var(--teal);
  }
  .contact__brand .brand-name { font-size: 24px; }
  .contact__brand .brand-name__mark { width: 16px; height: 16px; }
  .person__name {
    color: var(--teal); font-weight: 800; font-size: 22px; line-height: 1.1;
  }
  .person__place { font-size: 12px; margin-top: 2px; }
  .contact__list { list-style: none; margin-top: 20px; font-size: 12.5px; }
  .contact__list li { display: flex; align-items: center; gap: 8px; line-height: 1.55; }
  .contact__list svg { width: 11px; height: 11px; flex: none; fill: var(--teal); }
  .contact__address { font-size: 12.5px; margin-top: 16px; line-height: 1.5; }

  /* Logo side */
  .card--logo {
    display: flex; flex-direction: column; align-items: center; justify-content: center;
  }
  .card--logo .brand-name { font-size: 34px; }
  .card--logo .brand-name__mark { width: 22px; height: 22px; }
  .services {
    margin-top: 40px;
    color: var(--teal);
    font-size: 15.5px; font-weight: 400;
    letter-spacing: 0.01em;
  }
</style>
</head>
<body>
<main class="sheet">
  <section class="card card--contact" aria-label="Business card, contact side">
    <div class="contact__brand">
      <div class="brand-name"><span class="brand-name__mark"></span><span>Birchline<br>Septic<br>Solutions</span></div>
    </div>
    <div class="contact__divider"></div>
    <div class="contact__details">
      <p class="person__name">Colin Vandro</p>
      <p class="person__place">Maple Hollow</p>
      <ul class="contact__list">
        <li><svg viewBox="0 0 24 24" aria-hidden="true"><path d="M6.6 10.8a15 15 0 0 0 6.6 6.6l2.2-2.2c.3-.3.7-.4 1-.2 1.1.4 2.3.6 3.6.6.6 0 1 .4 1 1V20c0 .6-.4 1-1 1A17 17 0 0 1 3 4c0-.6.4-1 1-1h3.5c.6 0 1 .4 1 1 0 1.3.2 2.5.6 3.6.1.3 0 .7-.2 1z"/></svg>555-214-0387</li>
        <li><svg viewBox="0 0 24 24" aria-hidden="true"><path d="M2 5h20v14H2z M2 5l10 8 10-8" stroke="#161616" stroke-width="1.6"/></svg>info@birchlineseptic.com</li>
        <li><svg viewBox="0 0 24 24" aria-hidden="true"><circle cx="12" cy="12" r="10"/><path d="M2 12h20M12 2c3 3 3 17 0 20M12 2c-3 3-3 17 0 20" stroke="#161616" stroke-width="1.4" fill="none"/></svg>www.birchlineseptic.com</li>
      </ul>
      <p class="contact__address">Your address, City<br>State, Zip 1234</p>
    </div>
  </section>

  <section class="card card--logo" aria-label="Business card, logo side">
    <div class="brand-name"><span class="brand-name__mark"></span><span>Birchline<br>Septic Solutions</span></div>
    <p class="services">Services are pumping, inspections, installs, and repairs</p>
  </section>
</main>
</body>
</html>
```